Build Distinctive Business Card: Public Relations Government Relations firm

I have logo and colors done (attached) need a very cool way to present it on a business card (can be two sided if need be).

Public Relations Government Relations firm

Info:

Paul Marchetti, CEO
Keystone Public Relations
2730 West Harlan Blvd.
Pasadena CA 91105
(o) 213.555.0148
(f) 213.555.0173
paul@keystonekpr-example.com

Target Market(s)

Government relations, public relations, lobbyist, I was a past State Senator

Industry/Entity Type

Business

Contact Information for Business Card

Info:

Paul Marchetti, CEO
Keystone Public Relations
2730 West Harlan Blvd.
Pasadena CA 91105
(o) 213.555.0148
(f) 213.555.0173
paul@keystonekpr-example.com
@paulmarchetti

Requirements
Must have
• A sense of balance given logo is already done.
• It's a government relations firm really.
• Lobbyist type.
• Senatorial type...

```html
<!DOCTYPE html>
<html lang="en">
<head>
<meta charset="utf-8">
<title>Keystone Public Relations – Business Card</title>
<link href="https://fonts.googleapis.com/css2?family=Open+Sans:wght@400;600&display=swap" rel="stylesheet">
<style>
  :root {
    --page-bg: #0a0a0a;
    --card-bg: #1d1e20;
    --card-edge: #3a3c40;
    --panel-ring: #15191f;
    --accent-blue: #1a86cf;
    --text-blue: #1f87c9;
  }
  html, body {
    margin: 0;
    padding: 0;
    width: 1200px;
    height: 902px;
    overflow: hidden;
    background: var(--page-bg);
  }
  .business-card {
    position: absolute;
    left: 50px;
    top: 137px;
    width: 1100px;
    height: 627px;
    border-radius: 20px;
    overflow: hidden;
    background: var(--card-bg);
    box-shadow: inset 0 0 0 2px var(--card-edge);
    font-family: "Open Sans", Verdana, sans-serif;
  }
  .card-art {
    position: absolute;
    inset: 0;
  }
  .brand {
    position: absolute;
    left: 80px;
    top: 230px;
    display: flex;
    align-items: center;
    gap: 18px;
  }
  .brand-dot {
    width: 130px;
    height: 130px;
    border-radius: 50%;
    background: var(--accent-blue);
    flex: none;
  }
  .brand-name {
    color: var(--text-blue);
    font-weight: 600;
    line-height: 1;
  }
  .brand-name .word {
    display: block;
    font-size: 60px;
    letter-spacing: -0.5px;
  }
  .brand-name .line {
    display: block;
    font-size: 16px;
    letter-spacing: 3.5px;
    margin-top: 8px;
    padding-left: 30px;
  }
  .contact {
    position: absolute;
    left: 642px;
    top: 118px;
    color: var(--text-blue);
    white-space: nowrap;
  }
  .person-name {
    margin: 0;
    font-size: 46px;
    font-weight: 600;
    line-height: 1.1;
  }
  .person-title {
    margin: 0 0 0 5px;
    font-size: 27px;
    line-height: 1.2;
  }
  .address {
    margin: 62px 0 0 0;
    font-style: normal;
    font-size: 26px;
    line-height: 38px;
  }
  .reach {
    list-style: none;
    margin: 30px 0 0 0;
    padding: 0;
    font-size: 26px;
    line-height: 49px;
  }
  .reach li {
    display: flex;
    align-items: center;
    gap: 14px;
    padding-left: 8px;
  }
  .reach svg {
    width: 26px;
    height: 26px;
    flex: none;
    fill: var(--text-blue);
  }
</style>
</head>
<body>
  <div class="business-card">
    <svg class="card-art" viewBox="0 0 1100 627" aria-hidden="true">
      <defs>
        <linearGradient id="arc-blue" x1="0" y1="0" x2="0" y2="1">
          <stop offset="0" stop-color="#1371b5"/>
          <stop offset="0.5" stop-color="#2aa3e6"/>
          <stop offset="1" stop-color="#1371b5"/>
        </linearGradient>
        <radialGradient id="panel-fill" cx="0.3" cy="0.5" r="0.8">
          <stop offset="0" stop-color="#26303d"/>
          <stop offset="1" stop-color="#1b222c"/>
        </radialGradient>
      </defs>
      <circle class="accent-arc" cx="213" cy="312" r="412" fill="url(#arc-blue)"/>
      <circle class="panel-ring" cx="213" cy="312" r="375" fill="var(--panel-ring)"/>
      <circle class="panel" cx="213" cy="312" r="345" fill="url(#panel-fill)"/>
    </svg>

    <div class="brand">
      <span class="brand-dot"></span>
      <span class="brand-name">
        <span class="word">Keystone</span>
        <span class="line">PUBLIC RELATIONS</span>
      </span>
    </div>

    <div class="contact">
      <h1 class="person-name">Paul Marchetti</h1>
      <p class="person-title">CEO</p>
      <address class="address">
        2730 West Harlan Blvd<br>
        Pasadena CA 91105
      </address>
      <ul class="reach">
        <li>
          <svg viewBox="0 0 24 24" aria-label="Office phone"><path d="M6.6 10.8c1.4 2.8 3.8 5.1 6.6 6.6l2.2-2.2c.3-.3.7-.4 1-.2 1.1.4 2.3.6 3.6.6.6 0 1 .4 1 1V20c0 .6-.4 1-1 1C10.6 21 3 13.4 3 4c0-.6.4-1 1-1h3.5c.6 0 1 .4 1 1 0 1.3.2 2.5.6 3.6.1.3 0 .7-.2 1l-2.3 2.2z"/></svg>
          <span>213.555.0148</span>
        </li>
        <li>
          <svg viewBox="0 0 24 24" aria-label="Fax"><path d="M6.6 10.8c1.4 2.8 3.8 5.1 6.6 6.6l2.2-2.2c.3-.3.7-.4 1-.2 1.1.4 2.3.6 3.6.6.6 0 1 .4 1 1V20c0 .6-.4 1-1 1C10.6 21 3 13.4 3 4c0-.6.4-1 1-1h3.5c.6 0 1 .4 1 1 0 1.3.2 2.5.6 3.6.1.3 0 .7-.2 1l-2.3 2.2z"/></svg>
          <span>213.555.0173</span>
        </li>
        <li>
          <svg viewBox="0 0 24 24" aria-label="Email"><path d="M2 5h20v2.2l-10 7-10-7z"/><path d="M2 9.6l10 7 10-7V19H2z"/></svg>
          <span>paul@keystonekpr-example.com</span>
        </li>
      </ul>
    </div>
  </div>
</body>
</html>
```